Business Card Design

IT Solutions company.

I need a professional looking design with my company logo if possible.

Logo is located here:
http://www.brunelwavesystems.co.uk/dev/images/logo1.jpg
Feel free to redesign the logo if you think you have any better suggestions.

Our services include, IT Infrastructure/Telephony Maintenance & Hosting Services. Linux and Windows Solutions, App Development.

Out website is currently under development:
http://www.brunelwavesystems.co.uk/dev/

I'm looking for a colourful but professional looking business card.

Industry/Entity Type

Business

Contact Information for Business Card

BW Brunel Wavesystems Ltd
Martin Hollisby
07700958312
www.brunelwavesystems.co.uk
mhollisby@brunelwavesystems.co.uk

```html
<!DOCTYPE html>
<html lang="en">
<head>
<meta charset="utf-8">
<title>BW Brunel Wavesystems Ltd – Business Card</title>
<link rel="stylesheet" href="https://fonts.googleapis.com/css2?family=Arimo:wght@400;700&display=swap">
<style>
  :root {
    --backdrop: #e9e7e4;
    --card-white: #ffffff;
    --brand-blue: #1f4ff0;
    --charcoal: #333333;
    --ink: #222222;
    --rule: #d0d0d0;
    --on-blue: #ffffff;
  }
  * { box-sizing: border-box; margin: 0; padding: 0; }
  html, body {
    width: 1200px; height: 486px; overflow: hidden;
    background: var(--backdrop);
    font-family: "Arimo", Arial, sans-serif;
  }
  .canvas {
    position: relative; width: 1200px; height: 486px;
    display: flex; justify-content: center; align-items: center; gap: 50px;
  }
  .card {
    position: relative; width: 525px; height: 300px; overflow: hidden;
    box-shadow: 0 6px 18px rgba(0,0,0,.18);
  }

  /* Front */
  .card--front { background: var(--card-white); }
  .brand {
    position: absolute; display: flex; align-items: center; gap: 8px;
    color: var(--charcoal); font-weight: 700;
  }
  .brand__dot { border-radius: 50%; background: var(--brand-blue); flex: none; }
  .card--front .brand { left: 30px; top: 108px; font-size: 18px; line-height: 1.15; width: 205px; }
  .card--front .brand__dot { width: 32px; height: 32px; }
  .divider {
    position: absolute; left: 244px; top: 60px; width: 1px; height: 118px;
    background: var(--rule);
  }
  .contacts {
    position: absolute; left: 260px; right: 24px; top: 70px; list-style: none;
    font-size: 12.5px; color: var(--ink);
  }
  .contacts li { display: flex; align-items: center; gap: 8px; height: 30px; white-space: nowrap; }
  .contacts svg { width: 12px; height: 12px; fill: var(--charcoal); flex: none; }
  .front-bands { position: absolute; left: 0; bottom: 0; width: 525px; height: 80px; }
  .holder-name {
    position: absolute; right: 34px; bottom: 44px;
    color: var(--on-blue); font-weight: 700; font-size: 19px;
  }

  /* Back */
  .card--back { background: var(--brand-blue); color: var(--on-blue); text-align: center; }
  .card--back .brand {
    left: 0; right: 0; top: 40px; justify-content: center;
    color: var(--on-blue); font-size: 26px;
  }
  .card--back .brand__dot { width: 40px; height: 40px; background: var(--on-blue); }
  .back-url { position: absolute; left: 0; right: 0; top: 122px; font-weight: 700; font-size: 14px; }
  .services-title {
    position: absolute; left: 50%; top: 158px; transform: translateX(-50%);
    font-weight: 700; font-size: 14px; padding: 0 18px 6px;
    border-bottom: 1px solid var(--on-blue); white-space: nowrap;
  }
  .services {
    position: absolute; left: 0; right: 0; top: 190px; list-style: none;
    font-weight: 700; font-size: 14px; line-height: 21px;
  }
  .services li::before { content: "• "; }
</style>
</head>
<body>
<main class="canvas">
  <section class="card card--front" aria-label="Business card front">
    <div class="brand"><span class="brand__dot"></span><span>BW Brunel Wavesystems Ltd</span></div>
    <div class="divider"></div>
    <ul class="contacts">
      <li><svg viewBox="0 0 16 16"><path d="M4 1l3 3-2 2c1 2 3 4 5 5l2-2 3 3-2 2C7 14 2 9 2 3z"/></svg>07700958312</li>
      <li><svg viewBox="0 0 16 16"><path d="M1 4h14v9H1zM2 5l6 4 6-4v-.5H2z" fill-rule="evenodd"/></svg>mhollisby@brunelwavesystems.co.uk</li>
      <li><svg viewBox="0 0 16 16"><circle cx="8" cy="8" r="7"/><path d="M1 8h14M8 1v14M3 4h10M3 12h10" stroke="#fff" stroke-width="1" fill="none"/></svg>www.brunelwavesystems.co.uk</li>
    </ul>
    <svg class="front-bands" viewBox="0 0 525 80" preserveAspectRatio="none" aria-hidden="true">
      <polygon points="0,60 525,42 525,80 0,80" fill="var(--brand-blue)"/>
      <polygon points="0,46 240,46 226,60 0,60" fill="var(--charcoal)"/>
      <polygon points="0,60 226,60 222,64 0,64" fill="var(--card-white)"/>
      <polygon points="260,20 525,0 525,80 210,80" fill="var(--brand-blue)"/>
    </svg>
    <div class="holder-name">Martin Hollisby</div>
  </section>

  <section class="card card--back" aria-label="Business card back">
    <div class="brand"><span class="brand__dot"></span><span>BW Brunel Wavesystems Ltd</span></div>
    <div class="back-url">www.brunelwavesystems.co.uk</div>
    <div class="services-title">Our Services Include</div>
    <ul class="services">
      <li>IT Infrastructure/Telephony Maintenance</li>
      <li>Hosting Services</li>
      <li>Linux and Windows Solutions</li>
      <li>App Development</li>
    </ul>
  </section>
</main>
</body>
</html>
```